New Company Business Card design

Looking for a corporate looking business card utilising my new logo design - the logo i would like embossed as one option and flat as another - simplistic but stylish - less is more - we are an import export business launching into the market - i would like a couple of options as main background - Grey or Black

```html
<!DOCTYPE html>
<html lang="en">
<head>
<meta charset="utf-8">
<title>Meridian Trade Partners – Business Card</title>
<link rel="stylesheet" href="https://fonts.googleapis.com/css2?family=Cinzel:wght@400;500&family=Arimo:wght@400&display=swap">
<style>
  :root {
    --backdrop: #2f2f2f;
    --brand-blue: #1d77bc;
    --soft-grey: #dedede;
    --paper: #ffffff;
  }
  * { margin: 0; padding: 0; box-sizing: border-box; }
  html, body { width: 1200px; height: 802px; overflow: hidden; }
  body { background: var(--backdrop); position: relative; }

  .card {
    position: absolute;
    top: 274px;
    width: 443px;
    height: 265px;
    overflow: hidden;
  }
  .card--front { left: 136px; background: var(--brand-blue); }
  .card--back { left: 624px; background: var(--paper); }

  .front-decoration {
    position: absolute;
    left: 0; top: 0;
    width: 170px; height: 100%;
    background: linear-gradient(90deg, var(--soft-grey) 0%, #c9d9e8 55%, var(--brand-blue) 100%);
  }

  .contact-block {
    position: absolute;
    right: 35px;
    top: 108px;
    text-align: right;
    color: var(--paper);
  }
  .contact-name {
    font-family: "Cinzel", serif;
    font-weight: 500;
    font-size: 17px;
    letter-spacing: 0.5px;
    line-height: 1;
  }
  .contact-role {
    font-family: "Arimo", sans-serif;
    font-size: 12.5px;
    margin-top: 4px;
  }
  .contact-list {
    list-style: none;
    margin-top: 22px;
    font-family: "Arimo", sans-serif;
    font-size: 12.5px;
  }
  .contact-list li {
    display: flex;
    justify-content: flex-end;
    align-items: center;
    gap: 4px;
    height: 16px;
  }
  .contact-icon { width: 10px; height: 10px; fill: var(--paper); }

  .brand-lockup {
    position: absolute;
    left: 0; right: 0;
    top: 116px;
    display: flex;
    justify-content: center;
    align-items: center;
    gap: 10px;
  }
  .brand-dot {
    width: 16px; height: 16px;
    border-radius: 50%;
    background: var(--brand-blue);
  }
  .brand-name {
    font-family: "Cinzel", serif;
    font-weight: 500;
    font-size: 18px;
    color: var(--brand-blue);
    letter-spacing: 0.5px;
  }
</style>
</head>
<body>
  <section class="card card--front">
    <div class="front-decoration" role="img" aria-label="Decorative brand colour field"></div>
    <div class="contact-block">
      <div class="contact-name">Daniel Reyes</div>
      <div class="contact-role">Managing Director</div>
      <ul class="contact-list">
        <li>044-555 210 340
          <svg class="contact-icon" viewBox="0 0 10 10"><path d="M1 4 C1 1.5 9 1.5 9 4 L7 4.5 L6.5 3.5 L3.5 3.5 L3 4.5 Z M2.5 5 H7.5 L8.5 9 H1.5 Z"/></svg>
        </li>
        <li>044-555 210 341
          <svg class="contact-icon" viewBox="0 0 10 10"><path d="M2.5 0.5 H7.5 V9.5 H2.5 Z M3.5 1.5 V7.5 H6.5 V1.5 Z M4.5 8.1 H5.5 V8.9 H4.5 Z" fill-rule="evenodd"/></svg>
        </li>
        <li>hello@meridiantrade.com
          <svg class="contact-icon" viewBox="0 0 10 10"><path d="M0.5 2 H9.5 V8.5 H0.5 Z M1.2 2.6 L5 5.6 L8.8 2.6" fill-rule="evenodd"/><path d="M1.2 2.8 L5 5.8 L8.8 2.8" stroke="#1d77bc" stroke-width="0.9" fill="none"/></svg>
        </li>
        <li>www.meridiantrade.com
          <svg class="contact-icon" viewBox="0 0 10 10"><circle cx="5" cy="5" r="4.5"/><path d="M3 3 Q5 2 6 4 Q4.5 5 5.5 7 Q3.5 7 3 5 Z" fill="#1d77bc"/></svg>
        </li>
      </ul>
    </div>
  </section>

  <section class="card card--back">
    <div class="brand-lockup">
      <span class="brand-dot"></span>
      <span class="brand-name">Meridian Trade Partners</span>
    </div>
  </section>
</body>
</html>
```